Zielgruppe
Das Glas ist ein ständiger Begleiter in unserem Alltag.
Oft wird es zum Lustobjekt: tolle gesellschaftliche Momente, nette Menschen, gute Gespräche, erfrischende Getränke, schönes Glas. Einfach ein Genuss - für viele Sinne.
Seit über 100 Jahren widmen wir uns diesem schönen Kulturgut mit Leib und Seele. Deshalb fertigen wir ausschließlich in Deutschland kompromisslose Kristallgläser in höchster Perfektion - für eine genussvolle und entspannte Zeit im Kreise von Familie und Freunden.
Aufgabenstellung
Das Briefing ist offen für Ihre Kreativität. Wir sind auf der Suche nach cleveren Sprüchen, witzigen Wortspielen und einfachen, aber ansprechenden Designs.

```html
<!DOCTYPE html>
<html lang="de">
<head>
<meta charset="utf-8">
<title>Fill me up – Glasband</title>
<link rel="stylesheet" href="https://fonts.googleapis.com/css2?family=Josefin+Sans:wght@300;600&display=swap">
<style>
  :root {
    --paper: #ffffff;
    --ink: #1a1a1a;
    --guide: #6e6e6e;
    --glass-area: #f3f3f3;
  }
  html, body {
    margin: 0;
    padding: 0;
    width: 1200px;
    height: 1129px;
    overflow: hidden;
    background: var(--paper);
  }
  .sheet {
    display: block;
    width: 1200px;
    height: 1129px;
  }
  .glass-template { fill: var(--glass-area); }
  .print-band {
    fill: none;
    stroke: var(--guide);
    stroke-width: 1;
    stroke-dasharray: 6 5;
  }
  .fill-mark {
    stroke: var(--ink);
    stroke-width: 1;
  }
  .day-label {
    font-family: "Josefin Sans", sans-serif;
    font-weight: 300;
    font-size: 27px;
    fill: var(--ink);
  }
  .headline {
    font-family: "Josefin Sans", sans-serif;
    font-weight: 300;
    font-size: 34px;
    fill: var(--ink);
  }
  .brand-name {
    font-family: "Josefin Sans", sans-serif;
    font-weight: 600;
    font-size: 11px;
    letter-spacing: 1px;
    fill: var(--ink);
  }
</style>
</head>
<body>
<svg class="sheet" viewBox="0 0 1200 1129" xmlns="http://www.w3.org/2000/svg">
  <rect class="glass-template" x="422" y="101" width="367" height="937" role="img" aria-label="Umriss eines Weinglases mit Kelch, Stiel und Fuß"/>

  <rect class="print-band" x="56.5" y="192.5" width="1081" height="269"/>

  <g class="fill-marks">
    <line class="fill-mark" x1="459" y1="202.5" x2="885" y2="202.5"/>
    <text class="day-label" x="459" y="234" textLength="138" lengthAdjust="spacing">FRIDAY</text>

    <line class="fill-mark" x1="448" y1="294.5" x2="885" y2="294.5"/>
    <text class="day-label" x="448" y="326" textLength="203" lengthAdjust="spacing">SATURDAY</text>

    <line class="fill-mark" x1="438" y1="387.5" x2="885" y2="387.5"/>
    <text class="day-label" x="438" y="419" textLength="159" lengthAdjust="spacing">SUNDAY</text>
  </g>

  <text class="headline" transform="translate(161 432) rotate(-90)" textLength="208" lengthAdjust="spacing">FILL ME UP</text>

  <g class="brand">
    <rect class="print-band" x="56.5" y="277.5" width="44" height="98"/>
    <text class="brand-name" text-anchor="middle" transform="translate(83 326) rotate(-90)">FALBERGAU</text>
  </g>
</svg>
</body>
</html>
```